Visitenkarten-Design für virtuelle Jobmesse & Jobbörse für Soldaten
Zielgruppe
Die KVL GmbH ist ein Unternehmen das zwei Hauptprodukte betreibt! Zum einen Jobbörse für Soldaten unter www.laufbahnwechsel-beispiel.de und zum anderen eine virtuelle Jobmesse für Soldaten unter www.merivon-beispiel.de , die wir zweimal im Jahr veranstalten.
Aufgabenstellung
Wir haben ja die beiden Produkte Laufbahnwechsel.de und die Merivon, für die bereits jeweils ein separtes Logo besteht! Diese finden Sie im Anhang! Beide werden doch jedoch von einem Unternehmen, der KVL GmbH betrieben! Aktuell nutzen wir eine Visitenkarte mit dem Logo von KVL und eine mit dem Logo der MERIVON. Gerade im Hinblick darauf, dass wir zukünftig auch weiter Plattformen in unser Portfolio aufnehmen, möchte ich hier unsere V-Karten flexibler gestalten!
Ziel soll es also sein, eine Visitenkarte zu gestalten, auf dem klar wird, dass der Mitarbeiter von der KVL GmbH kommt, die KVL GmbH aber unterschiedliche Produkte betreibt.
Im Anhang finden Sie:
1. Das Logo von KVL
2. Das Logo von Merivon
3. Die aktuelle V-Karte von KVL
4. Die aktuelle V-Karte von MERIVON
Vielleicht ein kleiner Anreiz: Aktuell nutzen wir auch zwei getrennte Geschäftspapiere. Das von www.laufbahnwechsel-beispiel.de lade ich einmal hoch! Der Designer, der auch die Visitenkarte erstellt, erhällt im Anschluss den 1:1 Auftrag in Höhe von 200 Euro für die Erstellung des Geschäftspapiers! Wenn Sie jetzt schon einen Vorschlag für das Geschäftspapier einreichen, erhöht das natürlich Ihre Chancen, wobei ich verspreche, dass wir im Falle eine Annahme das 1:1 im Anschluß dennoch starten werden!

```html
<!DOCTYPE html>
<html lang="de">
<head>
<meta charset="utf-8">
<title>KVL GmbH – Visitenkarten</title>
<link href="https://fonts.googleapis.com/css2?family=Arimo:wght@400;700&display=swap" rel="stylesheet">
<style>
  :root {
    --brand-blue: #1f4a7d;
    --brand-blue-dark: #18365e;
    --back-blue: #20497c;
    --text-grey: #8a8a8a;
    --product-green: #3d5a2a;
    --border-grey: #555;
    --white: #ffffff;
  }
  html, body {
    margin: 0;
    padding: 0;
    overflow: hidden;
  }
  body {
    width: 848px;
    height: 1200px;
    background: var(--white);
    position: relative;
    font-family: "Arimo", Arial, sans-serif;
  }
  .card {
    position: absolute;
    width: 342px;
    height: 221px;
    box-sizing: border-box;
  }
  .card-front {
    left: 75px;
    background: var(--white);
    border: 1px solid var(--border-grey);
    overflow: hidden;
  }
  .card-back {
    left: 436px;
    background: var(--back-blue);
  }
  .row-1 { top: 198px; }
  .row-2 { top: 467px; }

  .arc {
    position: absolute;
    left: -1px;
    top: -1px;
    width: 170px;
    height: 221px;
  }
  .holder {
    position: absolute;
    left: 19px;
    color: var(--white);
  }
  .holder-name {
    margin: 0;
    font-weight: 700;
    font-size: 15px;
    line-height: 18.5px;
    letter-spacing: 0.4px;
  }
  .holder-position {
    margin: 0;
    font-size: 11px;
    line-height: 14px;
  }
  .company {
    position: absolute;
    left: 176px;
    top: 31px;
    color: var(--text-grey);
    font-size: 10.8px;
    white-space: nowrap;
  }
  .company-name {
    margin: 0 0 2px;
    color: var(--brand-blue);
    font-weight: 700;
    font-size: 20px;
    line-height: 24px;
  }
  .company-lines {
    margin: 0;
    line-height: 14.3px;
  }
  .company-lines + .company-lines {
    margin-top: 4px;
  }
  .company-web {
    letter-spacing: -0.3px;
  }
  .products {
    position: absolute;
    left: 176px;
    top: 178px;
    display: flex;
    align-items: center;
    gap: 12px;
    font-weight: 700;
    white-space: nowrap;
  }
  .product-jobs {
    color: var(--brand-blue);
    font-size: 8px;
  }
  .product-fair {
    display: flex;
    align-items: center;
    gap: 4px;
    color: var(--product-green);
    font-size: 10px;
    letter-spacing: 0.5px;
  }
  .product-dot {
    width: 7px;
    height: 7px;
    border-radius: 50%;
    background: var(--product-green);
  }
</style>
</head>
<body>

  <section class="card card-front row-1">
    <svg class="arc" viewBox="0 0 170 221" aria-hidden="true">
      <defs>
        <linearGradient id="arcFill1" x1="0" y1="0" x2="0" y2="1">
          <stop offset="0" stop-color="#1f4a7d"/>
          <stop offset="1" stop-color="#18365e"/>
        </linearGradient>
      </defs>
      <path d="M0 0 H121 C148 32 163 72 163 110 C163 150 146 190 112 222 H0 Z" fill="url(#arcFill1)"/>
    </svg>
    <div class="holder" style="top:88px">
      <p class="holder-name">Jonas Weidner</p>
      <p class="holder-position">Position</p>
    </div>
    <div class="company">
      <h2 class="company-name">KVL GmbH</h2>
      <p class="company-lines">Lindenweg 14<br>86999 Musterfeld</p>
      <p class="company-lines">Telefon 08400 - 123 45 67</p>
      <p class="company-lines">jonas.weidner@kvl.de<br><span class="company-web">www.laufbahnwechsel-beispiel.de</span><br>www.merivon-beispiel.de</p>
    </div>
    <div class="products">
      <span class="product-jobs">LAUFBAHN-BEISPIEL</span>
      <span class="product-fair">MERIVON<span class="product-dot"></span></span>
    </div>
  </section>
  <section class="card card-back row-1"></section>

  <section class="card card-front row-2">
    <svg class="arc" viewBox="0 0 170 221" aria-hidden="true">
      <defs>
        <linearGradient id="arcFill2" x1="0" y1="0" x2="0" y2="1">
          <stop offset="0" stop-color="#1f4a7d"/>
          <stop offset="1" stop-color="#18365e"/>
        </linearGradient>
      </defs>
      <path d="M0 0 H121 C148 32 163 72 163 110 C163 150 146 190 112 222 H0 Z" fill="url(#arcFill2)"/>
    </svg>
    <div class="holder" style="top:87px">
      <p class="holder-name">Maximillian<br>Mustermann</p>
      <p class="holder-position">Position</p>
    </div>
    <div class="company">
      <h2 class="company-name">KVL GmbH</h2>
      <p class="company-lines">Lindenweg 14<br>86999 Musterfeld</p>
      <p class="company-lines">Telefon 08400 - 123 45 67</p>
      <p class="company-lines">jonas.weidner@kvl.de<br><span class="company-web">www.laufbahnwechsel-beispiel.de</span><br>www.merivon-beispiel.de</p>
    </div>
    <div class="products">
      <span class="product-jobs">LAUFBAHN-BEISPIEL</span>
      <span class="product-fair">MERIVON<span class="product-dot"></span></span>
    </div>
  </section>
  <section class="card card-back row-2"></section>

</body>
</html>
```